Veterinary Pylon

My veterinary clinic is not clearly visible from the street and I want to place a Pylon next to my driveway. I want a modern, elegant straight Design, the Photo shows the sheduled place. One can see the clinic on our Homepage: www.tailbright-vethaus.at
The last pictures are examples for pylones I like

Target Market(s)

the passing cars often miss my entry...I want to show where to turn left

Colors
3276b5
33a6d7
00a990

Requirements
Must have
• High value, simple elegance, size: 250cm (high) x 100cm (width)
Nice to have
• Our Logo, arrow(?)

A special Text is not necessary but this will be an option:

Biegen sie hier ab und wir biegen es wieder hin!
Should not have
• Too much Color, the colors I have chosen are the possible colors but it‘s not necessary to use them.

```html
<!DOCTYPE html>
<html lang="de">
<head>
<meta charset="utf-8">
<title>Tailbright Vethaus – Pylon</title>
<link rel="stylesheet" href="https://fonts.googleapis.com/css2?family=Archivo:wdth,wght@125,900&display=swap">
<style>
  :root {
    --blue-deep: #1a62a3;
    --blue-bright: #29a2cd;
    --navy: #124c94;
    --circle-navy: #114a91;
    --cyan-line: #2ec5f0;
    --mist: #e6f4fa;
    --mist-light: #ecf6fb;
    --white: #ffffff;
  }
  html, body {
    margin: 0;
    padding: 0;
    width: 1200px;
    height: 3000px;
    overflow: hidden;
    background: var(--white);
  }
  .pylon {
    position: relative;
    width: 1200px;
    height: 3000px;
    overflow: hidden;
  }
  .pylon-shapes {
    position: absolute;
    inset: 0;
  }
  .brand-name {
    position: absolute;
    left: 0;
    right: 0;
    top: 560px;
    margin: 0;
    text-align: center;
    color: var(--white);
    font-family: "Archivo", "Arial Black", sans-serif;
    font-stretch: 125%;
    font-weight: 900;
    text-transform: uppercase;
    line-height: 1.05;
  }
  .brand-name .brand-main {
    display: block;
    font-size: 128px;
    letter-spacing: 2px;
  }
  .brand-name .brand-sub {
    display: block;
    font-size: 72px;
    letter-spacing: 22px;
    margin-top: 18px;
  }
</style>
</head>
<body>
<main class="pylon">
  <svg class="pylon-shapes" width="1200" height="3000" viewBox="0 0 1200 3000" aria-hidden="true">
    <defs>
      <linearGradient id="header-gradient" x1="0" y1="0" x2="1" y2="0">
        <stop offset="0" stop-color="#1a62a3"/>
        <stop offset="1" stop-color="#29a2cd"/>
      </linearGradient>
      <linearGradient id="base-gradient" x1="0" y1="0" x2="0" y2="1">
        <stop offset="0" stop-color="#e5f3f9"/>
        <stop offset="1" stop-color="#ecf6fb"/>
      </linearGradient>
    </defs>

    <!-- header band -->
    <path class="header-band" d="M0,0 H1200 V1165 Q660,1492 0,1116 Z" fill="url(#header-gradient)"/>
    <!-- navy accent curve -->
    <path class="header-accent" d="M0,1142 Q660,1520 1200,1188 V1237 Q660,1543 0,1153 Z" fill="var(--navy)"/>

    <!-- lower mist panel with cyan rim -->
    <path class="base-rim" d="M0,2045 Q600,1744 1200,2039 V2062 Q600,1765 0,2068 Z" fill="var(--cyan-line)"/>
    <path class="base-panel" d="M0,2068 Q600,1765 1200,2062 V3000 H0 Z" fill="url(#base-gradient)"/>

    <!-- turn-left sign -->
    <g class="turn-sign">
      <circle cx="609" cy="1907" r="212" fill="var(--circle-navy)"/>
      <path d="M733,1907 H498 M581,1824 L498,1907 L581,1990" fill="none" stroke="var(--white)" stroke-width="19" stroke-linecap="butt"/>
    </g>
  </svg>

  <h1 class="brand-name">
    <span class="brand-main">Tailbright</span>
    <span class="brand-sub">Vethaus</span>
  </h1>
</main>
</body>
</html>
```